Business Card for Professional Photographer

I'm looking for an eye catching modern clean design that compliments my logo/ website fonts & colours.
I specialise in architecture, corporate & commercial photography so I'm marketing to professional clients rather than portrait / wedding clients.

I would prefer to not have a solid black design.

My logo brand guide is as follows :

Main front font. : Reislust
Main font colour : #fff
Slogan front font : Ubuntu Bold
Monogram front font : Venti Medium
Container colour : #fff

I need print ready files in pdf .png & .eps formats.

Included in the files below are some screen grabs as reference to font & colours etc.

```html
<!DOCTYPE html>
<html lang="en">
<head>
<meta charset="utf-8">
<title>Northlight Studio – Business Card</title>
<link rel="stylesheet" href="https://fonts.googleapis.com/css2?family=Questrial&family=Ubuntu:wght@500;700&family=Roboto:wght@400&family=Roboto+Condensed:wght@700&display=swap">
<style>
  :root {
    --page: #3b3b3d;
    --card: #1c1c1e;
    --gold: #c9a04a;
    --gold-light: #e6c475;
    --gold-dark: #a27b2c;
    --white: #f4f4f4;
    --ink: #1b1b1b;
    --shade: rgba(18,18,20,.72);
  }
  * { margin: 0; padding: 0; box-sizing: border-box; }
  html, body { width: 799px; height: 1200px; overflow: hidden; }
  body { background: var(--page); position: relative; font-family: "Roboto", sans-serif; }

  .card {
    position: absolute;
    left: 60px;
    width: 679px;
    height: 388px;
    background: var(--card);
    border-radius: 4px;
    overflow: hidden;
    box-shadow: 0 18px 40px rgba(0,0,0,.45);
  }
  .card--front { top: 150px; }
  .card--back { top: 660px; background: linear-gradient(160deg, #232326 0%, var(--card) 70%); }

  .photo-collage {
    position: absolute; inset: 0;
    display: grid;
    grid-template-columns: 150px 190px 1fr;
    grid-template-rows: 120px 110px 1fr;
    gap: 3px;
    background: #141416;
  }
  .photo-tile { width: 100%; height: 100%; }
  .photo-tile--a { grid-column: 1; grid-row: 1; background: linear-gradient(135deg, #3a3630, #25262a); }
  .photo-tile--b { grid-column: 1; grid-row: 2 / 4; background: linear-gradient(160deg, #2a3850, #1d2635); }
  .photo-tile--c { grid-column: 2; grid-row: 1 / 3; background: linear-gradient(150deg, #4a4238, #2c2a27); }
  .photo-tile--d { grid-column: 2; grid-row: 3; background: linear-gradient(140deg, #3d3124, #26231f); }
  .photo-tile--e { grid-column: 3; grid-row: 1 / 3; background: linear-gradient(170deg, #3a4353, #232831); }
  .photo-tile--f { grid-column: 3; grid-row: 3; background: linear-gradient(130deg, #3b3530, #24221f); }
  .collage-shade { position: absolute; inset: 0; background: var(--shade); }

  .wordmark {
    font-family: "Questrial", sans-serif;
    color: var(--gold);
    letter-spacing: .16em;
    text-transform: uppercase;
    white-space: nowrap;
  }
  .tagline {
    font-family: "Ubuntu", sans-serif;
    font-weight: 500;
    color: var(--gold);
    letter-spacing: .18em;
    white-space: nowrap;
  }

  .front-brand { position: absolute; left: 130px; top: 120px; display: flex; align-items: center; gap: 18px; }
  .brand-dot { width: 22px; height: 22px; border-radius: 50%; background: var(--gold); flex: none; }
  .front-brand .wordmark { font-size: 36px; }
  .front-tagline { position: absolute; left: 170px; top: 170px; font-size: 13px; }
  .front-web {
    position: absolute; left: 0; right: 0; top: 290px; text-align: center;
    font-family: "Questrial", sans-serif; color: var(--gold); font-size: 20px; letter-spacing: .22em;
  }

  .person { position: absolute; left: 44px; top: 40px; }
  .person__name { font-family: "Roboto Condensed", sans-serif; font-weight: 700; font-size: 20px; color: var(--gold); }
  .person__role { font-size: 14px; color: var(--white); margin-top: 2px; }

  .contacts { position: absolute; left: 44px; top: 190px; list-style: none; }
  .contacts li { display: flex; align-items: center; gap: 14px; color: var(--white); font-size: 15px; height: 22px; }
  .contacts svg { width: 12px; height: 12px; flex: none; }

  .back-brand { position: absolute; right: 36px; top: 200px; text-align: right; }
  .back-brand .wordmark { font-size: 23px; letter-spacing: .09em; }
  .back-brand .tagline { font-size: 10px; margin-top: 5px; letter-spacing: .18em; }

  .gold-band { position: absolute; left: 0; bottom: 0; width: 100%; height: 100px; }
  .address {
    position: absolute; left: 330px; bottom: 22px;
    font-size: 16px; color: var(--ink); white-space: nowrap;
  }
</style>
</head>
<body>

  <section class="card card--front" aria-label="Card front">
    <div class="photo-collage">
      <div class="photo-tile photo-tile--a" role="img" aria-label="Interior photograph"></div>
      <div class="photo-tile photo-tile--b" role="img" aria-label="Waterfront photograph"></div>
      <div class="photo-tile photo-tile--c" role="img" aria-label="Architectural detail photograph"></div>
      <div class="photo-tile photo-tile--d" role="img" aria-label="Commercial interior photograph"></div>
      <div class="photo-tile photo-tile--e" role="img" aria-label="Modern building exterior photograph"></div>
      <div class="photo-tile photo-tile--f" role="img" aria-label="Corporate office photograph"></div>
    </div>
    <div class="collage-shade"></div>
    <div class="front-brand">
      <span class="brand-dot"></span>
      <span class="wordmark">Northlight Studio</span>
    </div>
    <div class="tagline front-tagline">Architecture Corporate Commercial</div>
    <div class="front-web">www.northlightstudio.com.au</div>
  </section>

  <section class="card card--back" aria-label="Card back">
    <div class="person">
      <div class="person__name">Mara Ellison</div>
      <div class="person__role">Photographer</div>
    </div>

    <ul class="contacts">
      <li>
        <svg viewBox="0 0 12 12"><path fill="#c9a04a" d="M2.5 1 4.3 1l.7 2.5-1.2 1a6 6 0 0 0 3.7 3.7l1-1.2 2.5.7v1.8c0 .8-.6 1.4-1.4 1.4A9.6 9.6 0 0 1 1 2.4C1 1.6 1.7 1 2.5 1Z"/></svg>
        0412555019
      </li>
      <li>
        <svg viewBox="0 0 12 12"><rect x="0.5" y="2" width="11" height="8" fill="#c9a04a"/><path d="M0.5 2 6 6.6 11.5 2" fill="none" stroke="#1c1c1e" stroke-width="1"/></svg>
        hello@northlightstudio.com.au
      </li>
      <li>
        <svg viewBox="0 0 12 12"><circle cx="6" cy="6" r="5.3" fill="#c9a04a"/><path d="M0.8 6h10.4M6 .7c-2.4 2.8-2.4 7.8 0 10.6M6 .7c2.4 2.8 2.4 7.8 0 10.6" fill="none" stroke="#1c1c1e" stroke-width=".8"/></svg>
        www.northlightstudio.com.au
      </li>
    </ul>

    <div class="back-brand">
      <div class="wordmark">Northlight Studio</div>
      <div class="tagline">Architecture Corporate Commercial</div>
    </div>

    <svg class="gold-band" viewBox="0 0 679 100" preserveAspectRatio="none" aria-hidden="true">
      <defs>
        <linearGradient id="goldGrad" x1="0" y1="0" x2="1" y2="0">
          <stop offset="0" stop-color="#a27b2c"/>
          <stop offset=".45" stop-color="#e6c475"/>
          <stop offset=".75" stop-color="#c9a04a"/>
          <stop offset="1" stop-color="#f0d48a"/>
        </linearGradient>
      </defs>
      <path d="M0 52 L300 52 Q312 52 318 44 L326 30 Q332 22 344 22 L679 22 L679 100 L0 100 Z" fill="url(#goldGrad)"/>
      <path d="M0 52 L300 52 Q312 52 318 44 L326 30 Q332 22 344 22 L679 22" fill="none" stroke="#1c1c1e" stroke-width="3"/>
      <rect x="0" y="58" width="679" height="42" fill="url(#goldGrad)"/>
    </svg>
    <div class="address">48 Harbour Lane Lorne Vic 3232</div>
  </section>

</body>
</html>
```